Wine Label Design-Hollow Creek Vineyard

Hollow Creek Vineyard is in the Barossa Valley in South Australia. The Barossa is recognized as Australia's premier wine region, producing Australia's icon wines and some " new takes on traditional".
This family owned and operated vineyard grows some exceptionally high quality fruit. Most of the fruit is sold and used for some of Australia's most iconic wines. Small quantities are retained by the owners for some wines with very limited availability. (Wines were previously sold as Brackwell Vineyards Hollow Creek ( Shiraz, Cabernet etc).

The wines will in the future be labeled simply ‘Hollow Creek Vineyard’. The label will launch this new identity for the single family single vineyard and its high quality wines which are a true expression of the vineyard and derive from the Hollow Creek common to this ancient area (800-2000 million years old).
The label should reflect
• Single vineyard, family owned
• vines in very old rock & soils
• High quality & reliability
• Edgy but true, design based thinking (Please note:blue is generally seen as an unacceptable colour for a wine label?? Don’t ask me why)

The wines will be sold mostly direct in Australia ( ie not through retail stores), with limited export to Asia, Scandinavia and Canada.
There are three quality levels and price points in the portfolio
1. Entry level premium for everyday drinking for discriminating drinkers-approx AUD20
2. Super Premium-approx AUD30
3. Limited Release ultlra premium-AUD75-90?
We envisage three variations on the label but with an obvious & common design element. This design element should be able to be used for corporate identification and promotion
The paper stock will be waterproof and self adhesive. Our preference is for designs that engage the user by appealing to both sight and touch. It is preferred that textures be added eg embossing, high build varnish etc-rather than be a facet of the stock itself.
For information on statutory label requirements refer to www.vintnerregistry-example.com . In brief
o Front label need not show any mandatory information. However we would prefer Variety, Barossa Valley, Year and alcohol to be shown on the front label
o Back label should show all mandatories and allow for a bar code
Updates

Project Deadline Extended
Reason: I've had a problem with my wireless broadband account and reception has been intermittent to say the least to the extent that I switched off at the weekend. Just going downtown now for a 'polite discussion' with my service provider.

Project Deadline Extended
Reason: I have receiver insufficient designs of quality which we would consider. Too many designs have a "cut and paste" appearance - too few exhibit an original art/design element which truly identifies the product.

Gals & Guys

most of the designs submitted lack punch and originality and are totally unmemorable.
Please-get on Searcho or whatever enter "Wine Label Designs" and do some research b4 u waste your time and mine. Formulaic cut and paste will not win the day. That's not to say that cut and paste can't work-but it must have some originality, impact and command attention. Please surprise me.

Following on from a question from a designer about who is our competition and what we are looking for I sent the following 
"I don't think I can add anything new. Read the brief and comments again and research wine labels on the web. In 30 minutes you'll get a good idea of the creative edgy designs in the industry. There are a plethora of collections. Our competition-anyone with a label. In 2010 there were over 2400 "producers" in other words 2400 producers with at least one label. In fact there are over 25000 Australian wines and then the numerous imported wines.

Target Market(s)

$20 people who budget everyday but have graduated from drinking 'entry level' wines. These people will likely fit into Cat. (b) in the $30 wine

$30 (a) will not over-compromise on some everyday discretionary expenditure.(b) might buy for special occasions

$70-$90 Professional/successful people with high disposable/discretionary income not particularly worried about recession. wine geeks.

Industry/Entity Type

Retail

Requirements
Must have
• identifiable element across range of wines

```html
<!DOCTYPE html>
<html lang="en">
<head>
<meta charset="utf-8">
<title>Hollow Creek Vineyard – Shiraz Label Set</title>
<link href="https://fonts.googleapis.com/css2?family=Cinzel:wght@400;600;700&family=Arimo:wght@400;700&display=swap" rel="stylesheet">
<style>
  :root{
    --page:#ffffff;
    --stage-light:#e4eaeb;
    --stage-mid:#a9b5b7;
    --stage-dark:#4b585a;
    --ink:#000000;
    --violet:#6b3cf5;
    --violet-deep:#4a1fd8;
    --lilac:#b79cf2;
    --lilac-pale:#ddd0fa;
    --amber:#c9892f;
    --amber-light:#e0a650;
    --cream:#f6ead2;
    --white:#ffffff;
    --motif:#8e9a9c;
  }
  *{box-sizing:border-box;margin:0;padding:0}
  html,body{width:1200px;height:951px;overflow:hidden;background:var(--page)}
  .canvas{position:relative;width:1200px;height:951px;background:var(--page)}
  .stage{
    position:absolute;left:53px;top:53px;width:1105px;height:854px;
    background:linear-gradient(125deg,var(--stage-light) 0%,var(--stage-mid) 55%,var(--stage-dark) 100%);
  }
  .motif{position:absolute;left:420px;top:170px;width:420px;height:500px}

  /* brand lockup */
  .brand{position:absolute;left:456px;top:126px;display:flex;align-items:center;gap:10px}
  .brand-square{width:44px;height:60px;background:var(--violet);border:3px solid var(--ink)}
  .brand-name{font-family:'Cinzel',serif;font-weight:600;color:var(--ink);line-height:1.1;font-size:21px}
  .brand-name span{display:block;font-size:20px;letter-spacing:1px}

  /* front label */
  .front{
    position:absolute;left:198px;top:226px;width:340px;height:479px;
    background:var(--ink);padding:11px;
  }
  .front-field{
    position:relative;width:100%;height:100%;
    background:radial-gradient(ellipse at center,var(--violet-deep) 0%,var(--violet) 55%,var(--lilac) 100%);
  }
  .front-title{
    position:absolute;left:0;right:0;top:15px;height:44px;
    background:linear-gradient(180deg,var(--amber-light),var(--amber));
    font-family:'Cinzel',serif;font-weight:400;color:var(--cream);
    font-size:31px;text-align:center;line-height:44px;letter-spacing:.5px;
  }
  .front-sub{
    position:absolute;left:0;right:0;top:74px;text-align:center;
    font-family:'Cinzel',serif;font-weight:700;color:var(--white);font-size:28px;line-height:34px;
    z-index:2;
  }
  .front-art{position:absolute;left:40px;top:90px;width:220px;height:370px}
  .front-foot{
    position:absolute;left:0;right:0;top:382px;height:53px;
    background:linear-gradient(180deg,var(--amber-light),var(--amber));
    font-family:'Cinzel',serif;color:var(--cream);font-size:18px;
    text-align:center;line-height:22px;padding-top:5px;letter-spacing:.5px;
  }

  /* back label */
  .back-top{
    position:absolute;left:711px;top:257px;width:242px;height:171px;
    background:var(--ink);padding:8px;
  }
  .back-heading{
    height:28px;background:linear-gradient(90deg,var(--lilac),var(--violet),var(--lilac));
    font-family:'Cinzel',serif;font-weight:600;color:var(--amber-light);
    font-size:11px;letter-spacing:-.2px;white-space:nowrap;overflow:hidden;
    text-align:center;line-height:28px;
  }
  .back-copy{
    font-family:'Arimo',sans-serif;color:var(--white);font-size:9.4px;line-height:13px;
    text-align:center;padding:9px 6px 0;
  }
  .back-band{
    position:absolute;left:8px;right:8px;bottom:8px;height:22px;
    background:linear-gradient(90deg,var(--lilac),var(--violet),var(--lilac));
  }
  .medallion{position:absolute;left:777px;top:405px;width:117px;height:94px}
  .back-bottom{
    position:absolute;left:711px;top:474px;width:242px;height:186px;
    background:var(--ink);padding:8px;
  }
  .back-field{
    position:relative;width:100%;height:100%;
    background:linear-gradient(180deg,var(--lilac-pale),var(--violet) 100%);
  }
  .back-measures{
    display:flex;justify-content:space-between;padding:6px 8px 0;
    font-family:'Arimo',sans-serif;font-weight:700;font-size:9.5px;color:var(--ink);line-height:11px;
  }
  .back-measures .drinks{text-align:left;width:60px}
  .back-info{
    position:absolute;left:0;right:0;top:30px;height:104px;
    background:linear-gradient(180deg,var(--amber-light),var(--amber));
    font-family:'Arimo',sans-serif;font-weight:700;font-size:9px;line-height:11px;color:var(--ink);
    padding:6px 8px;
  }
  .back-info p+p{margin-top:6px}
  .barcode-space{
    position:absolute;right:8px;top:10px;width:67px;height:86px;
    background:var(--white);
  }
</style>
</head>
<body>
<div class="canvas">
  <div class="stage">
    <svg class="motif" role="img" aria-label="Faint butterfly motif in the background" viewBox="0 0 420 500">
      <ellipse cx="210" cy="250" rx="190" ry="230" fill="var(--motif)" opacity=".28"/>
    </svg>
  </div>

  <div class="brand">
    <div class="brand-square"></div>
    <div class="brand-name">HOLLOW CREEK<span>VINEYARD</span></div>
  </div>

  <section class="front">
    <div class="front-field">
      <svg class="front-art" role="img" aria-label="Silhouette illustration of a hand holding a wine glass" viewBox="0 0 220 370">
        <defs>
          <linearGradient id="artTone" x1="0" y1="0" x2="1" y2="1">
            <stop offset="0" stop-color="#000"/>
            <stop offset=".6" stop-color="#1a0b3d"/>
            <stop offset="1" stop-color="#b79cf2"/>
          </linearGradient>
        </defs>
        <rect x="0" y="0" width="220" height="370" rx="90" fill="url(#artTone)"/>
      </svg>
      <h1 class="front-title">HOLLOW CREEK</h1>
      <h2 class="front-sub">VINEYARD</h2>
      <div class="front-foot">BAROSSA VALLEY<br>2012 SHIRAZ</div>
    </div>
  </section>

  <section class="back-top">
    <h3 class="back-heading">SHIRAZ 2012 BAROSSA VALLEY</h3>
    <p class="back-copy">Our Wines are planted on areas which are characterized by enormous quantities of shattered shale, slate, and limestone based rock. Which are major components in the unique flavor and our tight structure and minerality with abundant and generous fruit. Drinking well from the release and getting better from 2 to 12 years.</p>
    <div class="back-band"></div>
  </section>

  <svg class="medallion" role="img" aria-label="Oval medallion with small illustration of rocks and grapes" viewBox="0 0 117 94">
    <ellipse cx="58.5" cy="47" rx="56" ry="45" fill="var(--lilac-pale)"/>
    <ellipse cx="58.5" cy="47" rx="46" ry="38" fill="var(--amber)"/>
  </svg>

  <section class="back-bottom">
    <div class="back-field">
      <div class="back-measures"><span>750 ML.</span><span class="drinks">8.3 Standard Drinks</span></div>
      <div class="back-info">
        <p>Wine Of Australia<br>13.5 % Alc/Vol<br>Contains Sulfites<br>Produced With Milk Products</p>
        <p>Hollow Creek Vineyard<br>lot 3 Kestrel Ridge drive<br>Ellerby, SA<br>5399 Australia</p>
        <div class="barcode-space" aria-label="Space reserved for bar code"></div>
      </div>
    </div>
  </section>
</div>
</body>
</html>
```